Website redesign for job agency recruitment

Please refer to the attached document, “Tarvenly Work Website Brief,” for comprehensive details regarding the scope, objectives, and requirements of this website redesign project.

For imagery you can use images from this website https://www.pixelmarrowfoto.com or any other you regularly use.

Target Market(s)

Jobseekers and Companies looking for general labour

Industry/Entity Type

Services: Oil, Gas and Mining, Administrative, Construction and Trades, Warehouse and Logistics and, Manufacturing.

Number of Pages Required

5+ page

Font styles to use
Serif
Other font styles liked:
• Inter, Open-Sans or similar.

Requirements
Must have
• The requirements highlighted in the Word document attached. The final design needs to be provided in Figma including all viewports (Desktop, mobiel and tablet)
Should not have
• Website we like as a reference: www.brevicktalentco.com, www.qelvaworks.com, www.zunmarra.com, www.ferrowhires.com, www.9vtalentpool.com, www.hiringwithtrello.ca

```html
<!DOCTYPE html>
<html lang="en">
<head>
<meta charset="utf-8">
<title>Tarvenly Work Agency – Home</title>
<link href="https://fonts.googleapis.com/css2?family=Tinos:wght@700&family=Roboto:wght@400;500;700&display=swap" rel="stylesheet">
<style>
:root{
  --yellow:#f0bd16;
  --yellow-deep:#dcaa12;
  --blue:#0b2c94;
  --blue-dark:#07227a;
  --blue-light:#1d47b8;
  --ink:#141414;
  --text:#4a4a4a;
  --white:#ffffff;
  --serif:'Tinos', 'Times New Roman', serif;
  --sans:'Roboto', Arial, sans-serif;
}
*{margin:0;padding:0;box-sizing:border-box}
html,body{width:1200px;height:2963px;overflow:hidden}
body{position:relative;font-family:var(--sans);background:var(--white);color:var(--ink)}
.abs{position:absolute}
.section{position:absolute;left:0;width:1200px;overflow:hidden}

/* Hero */
.hero{top:0;height:640px;background:linear-gradient(180deg,#27408a 0%,#3a5aa8 30%,#4b4f78 60%,#7a5a3e 85%,#2a2a3a 100%)}
.hero-shade{inset:0;background:linear-gradient(90deg,rgba(10,20,60,.55) 0%,rgba(10,20,60,.15) 60%,rgba(10,20,60,0) 100%)}
.brand{left:144px;top:22px;width:125px;color:var(--white);font-family:var(--sans);font-weight:700;font-size:17px;line-height:1.15;display:flex;align-items:center;gap:8px}
.brand-dot{width:14px;height:14px;border-radius:50%;background:var(--yellow);flex:none}
.nav{left:330px;top:23px;display:flex;align-items:center;height:37px}
.nav a{font-family:var(--sans);font-weight:500;font-size:16px;color:var(--white);text-decoration:none;padding:0 20px;line-height:37px}
.nav a.is-active{background:var(--yellow);color:var(--ink);padding:0 15px;margin-right:5px}
.hero-title{left:144px;top:228px;font-family:var(--serif);font-size:43px;line-height:48px;color:var(--white)}
.hero-sub{left:144px;top:332px;font-weight:700;font-size:19px;color:var(--white)}
.btn{position:absolute;display:flex;align-items:center;justify-content:center;border-radius:26px;font-family:var(--sans);font-weight:500;font-size:16px;text-decoration:none}
.btn-yellow{background:var(--yellow);color:var(--ink)}
.btn-blue{background:var(--blue);color:var(--white)}
.slider-arrow{position:absolute;top:546px;width:38px;height:38px;border-radius:50%;background:var(--white);display:flex;align-items:center;justify-content:center}

/* Services */
.services{top:640px;height:774px;background:linear-gradient(120deg,#0a2a8c 0%,#0d2f9c 50%,#153ba8 100%)}
.section-title{width:1200px;left:0;text-align:center;font-family:var(--serif);font-size:46px}
.rule{height:2px;width:50px;background:var(--yellow)}
.tab{position:absolute;left:373px;width:225px;height:47px;border-radius:24px 0 0 24px;display:flex;align-items:center;justify-content:center;color:var(--white);font-weight:500;font-size:16px;background:linear-gradient(90deg,#0b2c94 60%,rgba(11,44,148,0) 100%)}
.tab.is-active{background:linear-gradient(90deg,#c99a14 0%,#e0ae16 40%,rgba(11,44,148,0) 100%)}
.service-card{left:600px;top:827px;width:242px;height:233px;background:var(--yellow);border-radius:36px;padding:30px 22px 0 26px;border:4px solid var(--blue);outline:0}
.service-card h3{font-weight:500;font-size:16px;color:var(--ink);margin-bottom:8px}
.service-card p{font-size:11.5px;line-height:16px;color:#2a2a2a}
.service-card a{display:inline-block;margin-top:8px;font-weight:700;font-size:11.5px;color:var(--ink);text-decoration:underline}

/* About */
.about{top:1414px;height:733px;background:var(--white)}
.about-text{left:144px;width:443px;font-size:15.5px;line-height:24px;color:var(--text);text-align:justify}

/* Apply */
.apply{top:2147px;height:364px;background:linear-gradient(135deg,#dcaa12 0%,#f0bd16 50%,#e8b514 100%)}

/* Footer */
.footer{top:2511px;height:452px;background:linear-gradient(160deg,#0a2a8c 0%,#0b2c94 60%,#153ba8 100%);color:var(--white)}
.footer-brand{left:140px;top:96px;font-size:23px;font-weight:500;color:var(--white);display:flex;align-items:center;gap:10px}
.social{position:absolute;top:72px;width:38px;height:38px;border-radius:50%;background:var(--blue-dark)}
.footer h4{position:absolute;top:96px;font-weight:500;font-size:23px;color:var(--white)}
.links{position:absolute;left:514px;top:150px;list-style:none}
.links li{display:flex;align-items:center;gap:16px;height:28px;font-size:16px}
.links svg{flex:none}
.contact{position:absolute;left:799px;top:150px}
.contact .city{font-weight:700;font-size:18px;height:28px;line-height:28px}
.contact-row{position:absolute;left:10px;display:flex;align-items:center;gap:18px;font-size:16px;white-space:nowrap}
.divider{left:144px;top:365px;width:912px;height:1px;background:rgba(255,255,255,.35)}
.copyright{left:0;width:1200px;top:395px;text-align:center;font-size:16px}
.copyright span{color:var(--yellow);text-decoration:underline}
</style>
</head>
<body>

<!-- Hero -->
<header class="section hero">
  <div class="abs hero-shade" role="img" aria-label="Dusk photograph of a downtown Canadian skyline with high-rise towers"></div>
  <div class="abs brand"><span class="brand-dot"></span>Tarvenly Work Agency Ltd.</div>
  <nav class="abs nav">
    <a class="is-active" href="#">Home</a>
    <a href="#">Candidates</a>
    <a href="#">Employers</a>
    <a href="#">Services Manufacturing</a>
    <a href="#">About Us</a>
    <a href="#">Contact Us</a>
  </nav>
  <h1 class="abs hero-title">Connecting Canada's<br>Workforce to Opportunity.</h1>
  <p class="abs hero-sub">AI-generated placeholder copy for now.</p>
  <a class="btn btn-yellow" href="#" style="left:144px;top:376px;width:182px;height:51px">For Candidates</a>
  <a class="btn btn-blue" href="#" style="left:335px;top:376px;width:182px;height:51px">For Employers</a>
  <div class="slider-arrow" style="left:556px"><svg width="14" height="14" viewBox="0 0 14 14"><path d="M9 2 4 7l5 5" fill="none" stroke="#222" stroke-width="1.8"/></svg></div>
  <div class="slider-arrow" style="left:605px"><svg width="14" height="14" viewBox="0 0 14 14"><path d="M5 2l5 5-5 5" fill="none" stroke="#222" stroke-width="1.8"/></svg></div>
</header>

<!-- Services -->
<section class="section services">
  <h2 class="abs section-title" style="top:80px;color:var(--white)">Our Services</h2>
  <div class="abs rule" style="left:575px;top:151px"></div>

  <svg class="abs" style="left:124px;top:169px" width="205" height="202" viewBox="0 0 205 202"><path d="M0 0H205L0 202Z" fill="var(--yellow)"/></svg>
  <div class="abs" style="left:144px;top:187px;width:297px;height:467px;border-radius:70px 0 0 70px;background:linear-gradient(180deg,#cfe3f7 0%,#a7c6e6 30%,#4a6fa8 65%,#1c3a78 100%)" role="img" aria-label="Upward view of glass office towers beneath a pale sky"></div>

  <div class="tab is-active" style="top:277px">Oil, Gas &amp; Mining</div>
  <div class="tab" style="top:357px">Administrative</div>
  <div class="tab" style="top:438px">Construction &amp; Trades</div>
  <div class="tab" style="top:517px">Warehouse &amp; Logistics</div>

  <svg class="abs" style="left:660px;top:270px" width="400" height="400" viewBox="0 0 400 400">
    <path d="M212 3 A197 197 0 1 1 7 217" fill="none" stroke="var(--white)" stroke-width="2.5"/>
  </svg>
  <div class="abs" style="left:684px;top:290px;width:354px;height:354px;border-radius:50%;background:linear-gradient(160deg,#d6dbe2 0%,#b4bcc8 40%,#c7622e 70%,#263457 100%)" role="img" aria-label="Two site workers in hard hats reviewing a tablet"></div>

  <div class="abs service-card" style="top:187px;left:596px;width:250px;height:241px">
    <h3>OIL, GAS &amp; MINING</h3>
    <p>As a specialist Division participating solely in the Oil, Gas &amp; Mining industry, we continuously meet the challenging staffing demands of Resource companies, Engineering Consultancies, Production sites, Drilling/Exploration companies and Specialty Products.</p>
    <a href="#">Read More &rsaquo;</a>
  </div>
</section>

<!-- About -->
<section class="section about">
  <h2 class="abs" style="left:144px;top:116px;font-family:var(--serif);font-size:46px;color:var(--ink)">About Us</h2>
  <div class="abs rule" style="left:144px;top:185px"></div>
  <p class="abs about-text" style="top:205px">Our staffing and recruitment services are not just limited to finding good people. We are a Canada-wide team of capable search specialists, career counselors, HR specialists, and business consultants who enjoy providing our clients with a very customized staffing solution that evolves within their market. Each project provides a chance for us to apply our knowledge and shine.</p>
  <p class="abs about-text" style="top:397px">With specialist divisions immersed into the heartbeat of five industries, we are the "go to" people who screen, interview, and successfully manage thousands of relationships each day. After meeting to target your desires and cross-referencing them with your needs, we will provide you with results that are on-time, on budget.</p>
  <a class="btn btn-yellow" href="#" style="left:144px;top:554px;width:182px;height:49px">Learn More &rsaquo;</a>

  <svg class="abs" style="left:610px;top:111px" width="136" height="136" viewBox="0 0 136 136"><g stroke="#e3e3e3" stroke-width="1" fill="none"><path d="M0 .5H136M0 45H136M0 90H136M.5 0V136M45 0V136M90 0V136M135 0V45"/></g></svg>
  <svg class="abs" style="left:874px;top:107px" width="203" height="201" viewBox="0 0 203 201"><path d="M0 0H203V201Z" fill="var(--yellow)"/></svg>
  <div class="abs" style="left:624px;top:128px;width:432px;height:476px;border-radius:0 60px 60px 0;background:linear-gradient(135deg,#1a1d24 0%,#2c3a52 45%,#4f6c96 75%,#c9ccd2 100%)" role="img" aria-label="Two colleagues smiling while working together at a laptop"></div>
</section>

<!-- Apply -->
<section class="section apply">
  <h2 class="abs section-title" style="top:84px;color:var(--ink)">Apply for Job</h2>
  <div class="abs rule" style="left:575px;top:150px;background:var(--ink)"></div>
  <p class="abs" style="left:0;width:1200px;top:170px;text-align:center;font-weight:500;font-size:19px;color:var(--ink)">Tarvenly Work Agency offer various opportunities in the different industries.</p>
  <a class="btn btn-blue" href="#" style="left:510px;top:216px;width:182px;height:50px">Apply Here &rsaquo;</a>
</section>

<!-- Footer -->
<footer class="section footer">
  <div class="abs footer-brand"><span class="brand-dot" style="width:16px;height:16px"></span>Tarvenly Work Agency Ltd.</div>
  <div class="social" style="left:144px;top:280px;background:var(--yellow)" role="img" aria-label="Social profile link"></div>
  <div class="social" style="left:193px;top:280px" role="img" aria-label="Social profile link"></div>
  <div class="social" style="left:241px;top:280px" role="img" aria-label="Social profile link"></div>

  <h4 style="left:514px">Quick Links</h4>
  <ul class="links">
    <li><svg width="14" height="12" viewBox="0 0 14 12"><path d="M1 6l4 4 8-9" fill="none" stroke="var(--yellow)" stroke-width="2.4"/></svg>Home</li>
    <li><svg width="14" height="12" viewBox="0 0 14 12"><path d="M1 6l4 4 8-9" fill="none" stroke="var(--yellow)" stroke-width="2.4"/></svg>Candidates</li>
    <li><svg width="14" height="12" viewBox="0 0 14 12"><path d="M1 6l4 4 8-9" fill="none" stroke="var(--yellow)" stroke-width="2.4"/></svg>Employers</li>
    <li><svg width="14" height="12" viewBox="0 0 14 12"><path d="M1 6l4 4 8-9" fill="none" stroke="var(--yellow)" stroke-width="2.4"/></svg>About us</li>
    <li><svg width="14" height="12" viewBox="0 0 14 12"><path d="M1 6l4 4 8-9" fill="none" stroke="var(--yellow)" stroke-width="2.4"/></svg>Vancouver Location</li>
    <li><svg width="14" height="12" viewBox="0 0 14 12"><path d="M1 6l4 4 8-9" fill="none" stroke="var(--yellow)" stroke-width="2.4"/></svg>Client Registration</li>
  </ul>

  <h4 style="left:798px">Contact Us</h4>
  <div class="contact">
    <div class="city">Calgary Location</div>
    <div class="city">Toronto Location</div>
    <div class="city">Vancouver Location</div>
  </div>
  <div class="contact-row" style="left:801px;top:243px">
    <svg width="16" height="12" viewBox="0 0 16 12"><rect x="0" y="0" width="16" height="12" rx="1.5" fill="var(--yellow)"/><path d="M1 1l7 6 7-6" fill="none" stroke="var(--blue)" stroke-width="1.4"/></svg>info@tarvenlywork.com
  </div>
  <div class="contact-row" style="left:801px;top:291px">
    <svg width="15" height="15" viewBox="0 0 15 15"><path d="M3 1l3 3-1.5 2c1 2 2.5 3.5 4.5 4.5L11 9l3 3-2 2C6 13 2 9 1 3z" fill="var(--yellow)"/></svg>604-555-0173
  </div>

  <div class="abs divider"></div>
  <p class="abs copyright">© Copyrights 2026 <span>Tarvenly Work Agency</span> | All Rights Reserved</p>
</footer>

</body>
</html>
```